Cutting Edge Property Services Provider is Looking to Update Business Card Design

We are looking to freshen up our business cards to match our cutting edge technology based image.

KORVANEX - Where Care Finds Its Pulse

More information about our company can be found on our website at www.korvanex-demo.net

We integrate technology in a historically low tech industry.

We have appeared on the Brisk 300/3000 list 2 years in a row and we're previously recognized as the 5th Quickest Rising Firm in San Diego.

Our core colors are blue and white, but are not against accents that might improve our image.

We currently have our Mission Statement on our Business Cards in a folding design:
KORVANEX IS THE LEADING BUILDING SERVICES INNOVATOR. BY COMBINING TECHNOLOGY WITH FUNCTIONAL TOOS THAT IMPROVE EFFICIENCY IN THE WORKPLACE, WE PROVIDE UNPARALLELED SERVICE IN THE INDUSTRY. DEVELOPING LASTING RELATIONSHIPS WITH OUR CLIENTS AND ASSOCIATES IS THE CORNERSTONE OF OUR SUCCESS.

We'd like to convey the image of a cutting edge, technology based company. Want the cards to pop.

Target Market(s)

Commercial Property Managers - 20 to 50 year old professionals

Industry/Entity Type

Business

Requirements
Must have
• Must utilize our logo obviously, but are definitely open to using variations on the logo. Utilizing the components of the logo, but maybe in different configurations or backgrounds, etc...

Must use the Name: KORVANEX.
Can also use KORVANEX PROPERTY SERVICES.

Must include the Mission Statement

Must say: Where Care Finds Its Pulse
Nice to have
• We are considering plastic stock, shaped cards, or folding cards.

Nothing over the top or really expensive, but will consider if it conveys innovation and technology.
Should not have
• No images of toilets, buildings, trees, or anything relating to commercial properties.

We want to convey our technology image.

```html
<!DOCTYPE html>
<html lang="en">
<head>
<meta charset="utf-8">
<title>KORVANEX Folding Business Card</title>
<link rel="stylesheet" href="https://fonts.googleapis.com/css2?family=Archivo+Black&family=Open+Sans:wght@400;600;700;800&display=swap">
<style>
  :root {
    --brand-blue: #0e4a7c;
    --brand-blue-deep: #0a3f6c;
    --text-blue: #1d4f80;
    --ink: #2a2a2a;
    --card-white: #ffffff;
    --mist: #dfe6ee;
    --mist-soft: #eef2f6;
    --swoosh-grey: #c9ccd0;
    --label-red: #e1252d;
    --stage: #2e2f31;
  }
  * { box-sizing: border-box; margin: 0; padding: 0; }
  html, body { width: 1200px; height: 805px; overflow: hidden; }
  body {
    background: var(--stage);
    position: relative;
    font-family: "Open Sans", Arial, sans-serif;
  }
  .panel-label {
    position: absolute;
    font-family: "Archivo Black", "Arial Black", sans-serif;
    color: var(--label-red);
    font-size: 32px;
    letter-spacing: 4px;
    width: 546px;
    text-align: center;
    line-height: 1;
  }
  .card {
    position: absolute;
    width: 546px;
    height: 310px;
    background: var(--card-white);
    border-radius: 24px;
    overflow: hidden;
  }
  .card--inner-top { left: 47px; top: 73px; }
  .card--front { left: 621px; top: 73px; }
  .card--inner-bottom { left: 47px; top: 404px; }
  .card--back { left: 621px; top: 404px; }

  .brand-block {
    position: absolute;
    background: var(--brand-blue);
    border-radius: 12px;
  }
  .brand-name {
    position: absolute;
    left: 0; width: 100%;
    text-align: center;
    font-weight: 800;
    color: var(--brand-blue);
    line-height: 1;
  }

  /* Inner top */
  .card--inner-top .brand-block { left: 125px; top: 49px; width: 302px; height: 151px; }
  .card--inner-top .brand-name { top: 208px; font-size: 38px; letter-spacing: 4px; }
  .card--inner-top .web-line {
    position: absolute; left: 0; width: 100%; top: 276px;
    text-align: center; font-size: 19px; letter-spacing: 3.5px; color: var(--ink); line-height: 1.2;
  }

  /* Front */
  .card--front .brand-block { left: 159px; top: 12px; width: 227px; height: 114px; }
  .card--front .brand-name { top: 134px; font-size: 25px; letter-spacing: 2px; }
  .contact-left {
    position: absolute; right: 270px; top: 176px;
    text-align: right; color: var(--ink);
  }
  .contact-left .person-name { font-size: 19px; font-weight: 700; color: var(--brand-blue); line-height: 1.1; }
  .contact-left .person-title { font-size: 12.5px; margin-top: 2px; line-height: 16px; }
  .contact-left .address { font-size: 13px; line-height: 18px; margin-top: 8px; }
  .contact-divider {
    position: absolute; left: 291px; top: 180px; width: 1px; height: 80px; background: #b9bec4;
  }
  .contact-right {
    position: absolute; left: 304px; top: 180px;
    list-style: none; font-size: 13px; color: var(--ink);
  }
  .contact-right li { display: flex; align-items: center; height: 28.5px; }
  .contact-right svg { width: 11px; height: 11px; margin-right: 7px; fill: var(--brand-blue-deep); }
  .front-wave { position: absolute; left: 0; top: 230px; width: 546px; height: 80px; }

  /* Inner bottom */
  .mission-backdrop {
    position: absolute; inset: 0;
    background: radial-gradient(ellipse 260px 130px at 50% 48%, var(--mist) 0%, var(--mist-soft) 55%, var(--card-white) 100%);
  }
  .mission {
    position: relative;
    padding-top: 62px;
    text-align: center;
    font-size: 16px;
    line-height: 30.2px;
    color: var(--text-blue);
  }

  /* Back */
  .back-backdrop {
    position: absolute; inset: 0;
    background: linear-gradient(180deg, var(--mist-soft) 0%, #f7f9fb 50%, var(--mist-soft) 100%);
  }
  .card--back .brand-name { top: 118px; font-size: 54px; letter-spacing: 4px; }
  .tagline {
    position: absolute; left: 0; width: 100%; top: 236px;
    text-align: center; font-size: 24px; font-weight: 700; color: var(--brand-blue-deep);
    letter-spacing: -0.3px; line-height: 1.2;
  }
</style>
</head>
<body>
  <div class="panel-label" style="left:47px; top:20px;">Inner Top</div>
  <div class="panel-label" style="left:621px; top:20px;">Front</div>
  <div class="panel-label" style="left:47px; top:734px;">Inner Bottom</div>
  <div class="panel-label" style="left:621px; top:734px;">Back</div>

  <section class="card card--inner-top">
    <div class="brand-block"></div>
    <div class="brand-name">KORVANEX</div>
    <div class="web-line">www.korvanex-demo.net</div>
  </section>

  <section class="card card--front">
    <div class="brand-block"></div>
    <div class="brand-name">KORVANEX</div>
    <svg class="front-wave" viewBox="0 0 546 80" preserveAspectRatio="none" aria-hidden="true">
      <path d="M0 22 C100 50 250 58 546 54 L546 80 L0 80 Z" fill="var(--swoosh-grey)"/>
      <path d="M0 44 C150 64 330 52 546 62 L546 80 L0 80 Z" fill="var(--brand-blue)"/>
    </svg>
    <div class="contact-left">
      <div class="person-name">Your Name</div>
      <div class="person-title">Title</div>
      <div class="address">2180 Halvorsen Ridge Rd<br>Suite 210, Marlow Bay, CA 90000</div>
    </div>
    <div class="contact-divider"></div>
    <ul class="contact-right">
      <li><svg viewBox="0 0 12 12"><path d="M2.5 1 L4.5 1 L5.3 3.6 L4 4.6 C4.7 6 6 7.3 7.4 8 L8.4 6.7 L11 7.5 L11 9.5 C11 10.3 10.3 11 9.5 11 C5 11 1 7 1 2.5 C1 1.7 1.7 1 2.5 1 Z"/></svg>1(866) 555-0142</li>
      <li><svg viewBox="0 0 12 12"><path d="M1 3 H11 V10 H1 Z M1.6 3.4 L6 7 L10.4 3.4" stroke="#fff" stroke-width="0.9"/></svg>info@korvanex-demo.net</li>
      <li><svg viewBox="0 0 12 12"><circle cx="6" cy="6" r="5"/><path d="M1 6 H11 M6 1 C3.5 3.5 3.5 8.5 6 11 M6 1 C8.5 3.5 8.5 8.5 6 11" stroke="#fff" stroke-width="0.8" fill="none"/></svg>www.korvanex-demo.net</li>
    </ul>
  </section>

  <section class="card card--inner-bottom">
    <div class="mission-backdrop" role="img" aria-label="Soft pale blue backdrop behind the mission statement"></div>
    <p class="mission">
      Korvanex is The Leading Building Services Innovator.<br>
      By Combining Technology With Functional Toos That<br>
      Improve Efficiency In The Workplace, We Provide<br>
      Unparalleled Service in The Industry. Developing<br>
      Lasting Relationships With Our Clients and Associates<br>
      is The Cornerstone of Our Success.
    </p>
  </section>

  <section class="card card--back">
    <div class="back-backdrop" role="img" aria-label="Faint pale blue repeating backdrop"></div>
    <div class="brand-name">KORVANEX</div>
    <div class="tagline">Where Care Finds Its Pulse</div>
  </section>
</body>
</html>
```